Business Card Design

New business card design

Target Market(s)

Residential & Commercial Property Managers

Industry/Entity Type

Plumbing Services

Contact Information for Business Card

Name - Rowan Keddle, title - Director, Phone Number - 0431 286 517, email - rowan@tbk-plumbing.com.au, Company ABN - 73 215 904 386,

Font styles to use
Sans Serif

Colors
0054AA
0677BA
7BADD7
CADEEF
E8F1F8

```html
<!DOCTYPE html>
<html lang="en">
<head>
<meta charset="utf-8">
<title>TBK Plumbing Services – Business Card</title>
<link href="https://fonts.googleapis.com/css2?family=Roboto:wght@300;400;700&display=swap" rel="stylesheet">
<style>
  :root {
    --stage: #3d3d3d;
    --card-white: #ffffff;
    --card-dark: #1e252c;
    --accent-blue: #1aa3e0;
    --ink-dark: #1e252c;
    --ink-light: #ffffff;
    --ink-muted: #c9d1d8;
    --drop-tone-a: #161b20;
    --drop-tone-b: #2f3d49;
  }
  * { box-sizing: border-box; margin: 0; padding: 0; }
  html, body {
    width: 1200px; height: 803px; overflow: hidden;
    background: var(--stage);
    font-family: "Roboto", Arial, sans-serif;
  }
  .stage {
    width: 1200px; height: 803px;
    display: flex; align-items: center; justify-content: center; gap: 40px;
  }
  .card {
    position: relative;
    width: 520px; height: 290px;
    border-radius: 18px;
    overflow: hidden;
    box-shadow: 0 14px 30px rgba(0,0,0,0.45);
  }
  .card-front { background: var(--card-white); }
  .front-shape { position: absolute; inset: 0; }
  .brand {
    position: absolute; left: 32px; top: 112px;
    display: flex; align-items: center; gap: 8px;
    white-space: nowrap;
  }
  .brand-name {
    font-size: 21px; font-weight: 400; color: var(--ink-dark);
    letter-spacing: 0.5px;
  }
  .brand-dot {
    width: 11px; height: 11px; border-radius: 50%;
    background: var(--accent-blue);
  }
  .contact {
    position: absolute; right: 26px; top: 92px;
    text-align: right; color: var(--ink-light);
  }
  .contact-name { font-size: 22px; font-weight: 700; letter-spacing: 0.3px; }
  .contact-title { font-size: 12px; font-weight: 300; color: var(--ink-muted); margin-top: 2px; }
  .contact-lines { margin-top: 16px; font-size: 12.5px; font-weight: 400; line-height: 1.65; }
  .contact-line { display: flex; justify-content: flex-end; align-items: center; gap: 7px; }
  .contact-icon { width: 11px; height: 11px; fill: var(--ink-light); }
  .card-back { background: var(--card-dark); }
  .back-pattern {
    position: absolute; inset: 0;
    background: linear-gradient(135deg, var(--drop-tone-a) 0%, var(--drop-tone-b) 100%);
  }
</style>
</head>
<body>
<main class="stage">
  <section class="card card-front" aria-label="Card front">
    <svg class="front-shape" viewBox="0 0 520 290" width="520" height="290" aria-hidden="true">
      <path d="M 352 0 C 330 130, 250 230, 176 290 L 520 290 L 520 0 Z" fill="var(--accent-blue)"/>
      <path d="M 360 0 C 338 132, 260 232, 188 290 L 520 290 L 520 0 Z" fill="var(--card-dark)"/>
    </svg>
    <div class="brand">
      <span class="brand-name">tbk plumbing services</span>
      <span class="brand-dot"></span>
    </div>
    <div class="contact">
      <p class="contact-name">Rowan Keddle</p>
      <p class="contact-title">Director</p>
      <div class="contact-lines">
        <p class="contact-line">ABN - 73 215 904 386</p>
        <p class="contact-line">0431 286 517
          <svg class="contact-icon" viewBox="0 0 24 24" aria-hidden="true"><path d="M6.6 10.8a15.1 15.1 0 0 0 6.6 6.6l2.2-2.2a1 1 0 0 1 1-.25 11.4 11.4 0 0 0 3.6.57 1 1 0 0 1 1 1V20a1 1 0 0 1-1 1A17 17 0 0 1 3 4a1 1 0 0 1 1-1h3.5a1 1 0 0 1 1 1c0 1.250.2 2.450.57 3.57a1 1 0 0 1-.25 1z"/></svg>
        </p>
        <p class="contact-line">rowan@tbk-plumbing.com.au
          <svg class="contact-icon" viewBox="0 0 24 24" aria-hidden="true"><path d="M2 5h20v14H2z M2 5l10 8 10-8" fill="none" stroke="#fff" stroke-width="2.4"/></svg>
        </p>
      </div>
    </div>
  </section>

  <section class="card card-back" aria-label="Card back">
    <div class="back-pattern" role="img" aria-label="Repeating water-drop pattern in dark slate tones"></div>
  </section>
</main>
</body>
</html>
```